Italian restaurant needs new site

Need to make our website better.

Must have reservation module

Must be able to sell wine tasting tours and wine pairing tours and intégrate with dunmo desk

Blog

Social media

Wandervane ranking and last review.
Updates

Number of Pages Required

1 page

Font styles to use
Serif

Requirements
Must have
• Reservation module
• Marketplace to buy wine pairings and gift certificates
• Wandervane review
• Kindlepost posts
• All info from old site

```html
<!DOCTYPE html>
<html lang="en">
<head>
<meta charset="utf-8">
<title>Vinoro Bistro — Italian Restaurant in Cabo San Lucas</title>
<link href="https://fonts.googleapis.com/css2?family=Lora:wght@400;500;700&family=Lato:wght@400;700&display=swap" rel="stylesheet">
<style>
:root{
  --wine:#7c1521;
  --wine-text:#8e1d28;
  --ink:#2b2b2b;
  --muted:#777;
  --soft:#f7f6f6;
  --line:#dcdcdc;
  --white:#fff;
}
*{box-sizing:border-box;margin:0;padding:0}
html,body{width:1200px;height:5187px;overflow:hidden}
body{position:relative;background:var(--white);font-family:"Lora",Georgia,serif;color:var(--ink)}
.abs{position:absolute}
.band{position:absolute;left:0;width:1200px}
.soft{background:var(--soft)}
.section-title{position:absolute;left:0;width:1200px;text-align:center;font-size:34px;font-weight:400;color:var(--wine-text)}
.rule{position:absolute;left:560px;width:80px;height:2px;background:var(--wine)}
.btn{position:absolute;display:flex;align-items:center;justify-content:center;background:var(--wine);color:var(--white);border-radius:6px;font-family:"Lora",Georgia,serif}
.photo{position:absolute}

/* header */
.brand{position:absolute;left:110px;top:34px;display:flex;align-items:center;gap:10px}
.brand-mark{width:14px;height:14px;border-radius:50%;background:var(--wine)}
.brand-name{font-size:22px;color:var(--wine-text)}
.nav{position:absolute;top:56px;font-size:17px;color:var(--ink)}
.nav.active{border-bottom:2px solid var(--ink);padding-bottom:8px}

/* hero */
.hero{position:absolute;left:0;top:131px;width:1200px;height:536px;background:radial-gradient(circle at 50% 48%,#b5552c 0,#8a3a1d 22%,#3b3331 45%,#222 100%)}
.hero-title{position:absolute;left:0;top:360px;width:1200px;text-align:center;font-size:70px;color:var(--white);font-weight:400}
.dot{position:absolute;top:556px;width:9px;height:9px;border-radius:50%;background:#fff}

/* intro */
.intro-title{position:absolute;top:744px;left:0;width:1200px;text-align:center;font-size:34px;color:var(--wine-text)}
.intro-sub{position:absolute;top:803px;left:0;width:1200px;text-align:center;font-size:20px;color:var(--muted)}
.intro-text{position:absolute;left:118px;top:880px;width:964px;text-align:center;font-size:15px;line-height:28px;color:#666}

/* cards */
.card-title{position:absolute;font-size:17px;color:var(--wine-text)}
.card-text{position:absolute;width:300px;font-family:"Lato",Arial,sans-serif;font-size:12px;line-height:19px;color:var(--muted)}
.card-btn{width:125px;height:42px;font-size:15px}

/* blog */
.post-title{position:absolute;font-size:29px;line-height:38px;color:var(--wine-text);width:260px}
.post-date{position:absolute;font-size:18px;color:var(--ink)}

/* form */
.field{position:absolute;height:62px;border:1px solid var(--line);border-radius:4px;background:var(--white);padding:18px 16px;font-family:"Lato",Arial,sans-serif;font-size:13px;color:#555}
.field svg{position:absolute;right:16px;top:25px}

/* reviews */
.rating-title{position:absolute;font-size:18px;color:var(--wine-text)}
.rating-sub{position:absolute;font-family:"Lato",Arial,sans-serif;font-size:13px;color:#555}
.reviews{position:absolute;left:443px;top:4565px;width:646px;height:190px;border:1px solid #e3e3e3;background:var(--white)}
.reviews-head{position:absolute;left:0;top:0;width:644px;height:68px;background:#f1f1f1;padding:24px 30px;font-size:17px;color:var(--wine-text)}
.rev-date{position:absolute;top:98px;font-family:"Lato",Arial,sans-serif;font-size:12px;color:#555}
.rev-quote{position:absolute;top:120px;font-size:17px;color:var(--ink)}

/* footer */
.foot-head{position:absolute;top:4898px;font-size:14px;color:var(--wine-text);font-weight:700}
.foot-list{position:absolute;top:4930px;font-family:"Lato",Arial,sans-serif;font-size:14px;line-height:24px;color:var(--ink);list-style:none}
.social-box{position:absolute;left:837px;top:4886px;width:252px;height:169px;background:var(--white);border:1px solid #e6e6e6}
.legal{position:absolute;top:5134px;font-family:"Lato",Arial,sans-serif;font-size:14px;color:var(--ink)}
</style>
</head>
<body>

<!-- Header -->
<header>
  <div class="brand"><span class="brand-mark"></span><span class="brand-name">Vinoro Bistro</span></div>
  <nav>
    <span class="nav active" style="left:834px">Home</span>
    <span class="nav" style="left:926px">Menu</span>
    <span class="nav" style="left:1020px">Reservation</span>
  </nav>
</header>

<!-- Hero -->
<section class="hero" role="img" aria-label="Overhead photo of a baked Italian dish on a dark table with a checked cloth, olives and chili peppers">
  <h1 class="hero-title">Vinoro Bistro</h1>
  <span class="dot" style="left:584px;top:425px"></span>
  <span class="dot" style="left:598px;top:425px;opacity:.6"></span>
  <span class="dot" style="left:612px;top:425px;opacity:.6"></span>
</section>

<!-- Intro -->
<section class="band soft" style="top:667px;height:550px"></section>
<h2 class="intro-title">Vinoro Bistro italian restaurant</h2>
<p class="intro-sub">In Cabo San Lucas</p>
<div class="rule" style="top:850px"></div>
<p class="intro-text">Vinoro Bistro Located in the heart of downtown, across from Plaza Serena, just two short blocks up from Harborline Resort and the Cabo marina is Vinoro Bistro, a place with great original Southern Italian and Mediterranean cuisine and a European touch. Save to enjoy your classic favorites or satisfy even the most distinctive pallet. We offer a variety of homemade fresh cooked dishes derived from generations-old family recipes, accompanied by an extensive specials selection of national and international wines and fun Italian inspired cocktails.</p>
<a class="btn" style="left:481px;top:1065px;width:238px;height:59px;font-size:19px">Read More</a>

<!-- Wine Tasting Tours -->
<h2 class="section-title" style="top:1298px">Wine Tasting Tours</h2>
<div class="rule" style="top:1369px"></div>
<div class="photo" style="left:110px;top:1411px;width:312px;height:207px;background:linear-gradient(135deg,#2a211d,#6b4a3a 55%,#c9a58a)" role="img" aria-label="Guests tasting red wine"></div>
<div class="photo" style="left:443px;top:1411px;width:311px;height:207px;background:linear-gradient(135deg,#7d6656,#c8b7a6 55%,#4a3a33)" role="img" aria-label="Friends toasting with wine glasses"></div>
<div class="photo" style="left:781px;top:1411px;width:312px;height:207px;background:linear-gradient(135deg,#e8dccc,#a8836a 55%,#5b2b26)" role="img" aria-label="Couple sharing a wine tasting"></div>
<h3 class="card-title" style="left:110px;top:1638px">Wine Tasting Tours</h3>
<h3 class="card-title" style="left:443px;top:1638px">Wine Tasting Tours</h3>
<h3 class="card-title" style="left:781px;top:1638px">Wine Tasting Tours</h3>
<p class="card-text" style="left:110px;top:1668px">Sed ut perspiciatis unde omnis iste natus error sit voluptatem</p>
<p class="card-text" style="left:443px;top:1668px">Sed ut perspiciatis unde omnis iste natus error sit voluptatem</p>
<p class="card-text" style="left:781px;top:1668px">Sed ut perspiciatis unde omnis iste natus error sit voluptatem</p>
<a class="btn card-btn" style="left:110px;top:1743px">Sell Now</a>
<a class="btn card-btn" style="left:443px;top:1743px">Sell Now</a>
<a class="btn card-btn" style="left:781px;top:1743px">Sell Now</a>

<!-- Wine Pairing Tours -->
<section class="band soft" style="top:1874px;height:650px"></section>
<h2 class="section-title" style="top:1965px">Wine Pairing Tours</h2>
<div class="rule" style="top:2037px"></div>
<div class="photo" style="left:110px;top:2078px;width:312px;height:208px;background:linear-gradient(135deg,#3f5a2a,#7f9a4a 50%,#2f4a6a)" role="img" aria-label="Couple with wine glasses in a vineyard"></div>
<div class="photo" style="left:443px;top:2078px;width:311px;height:208px;background:linear-gradient(135deg,#3a2514,#a57a3c 50%,#e2c98e)" role="img" aria-label="White wine glasses with cheese on a table"></div>
<div class="photo" style="left:781px;top:2078px;width:312px;height:208px;background:linear-gradient(135deg,#e9ecef,#7d8a52 50%,#3c2a1d)" role="img" aria-label="Wine bottle with grapes and bread"></div>
<h3 class="card-title" style="left:110px;top:2302px">Wine Pairing Tours 1</h3>
<h3 class="card-title" style="left:443px;top:2302px">Wine Pairing Tours 2</h3>
<h3 class="card-title" style="left:781px;top:2302px">Wine Pairing Tours 3</h3>
<p class="card-text" style="left:110px;top:2332px">Sed ut perspiciatis unde omnis iste natus error sit voluptatem</p>
<p class="card-text" style="left:443px;top:2332px">Sed ut perspiciatis unde omnis iste natus error sit voluptatem</p>
<p class="card-text" style="left:781px;top:2332px">Sed ut perspiciatis unde omnis iste natus error sit voluptatem</p>
<a class="btn card-btn" style="left:110px;top:2393px">Sell Now</a>
<a class="btn card-btn" style="left:443px;top:2393px">Sell Now</a>
<a class="btn card-btn" style="left:781px;top:2393px">Sell Now</a>

<!-- Blog -->
<h2 class="section-title" style="top:2612px">Blog</h2>
<div class="rule" style="top:2680px"></div>
<div class="photo" style="left:110px;top:2760px;width:208px;height:172px;background:linear-gradient(135deg,#3a1c16,#8a3e2a 50%,#d4b89a)" role="img" aria-label="Wine bottles resting in a rack"></div>
<div class="photo" style="left:615px;top:2760px;width:208px;height:172px;background:radial-gradient(circle at 50% 50%,#9d1020,#4a0810 45%,#6d7a3a 100%)" role="img" aria-label="Glass of red wine seen from above"></div>
<div class="photo" style="left:110px;top:2998px;width:208px;height:173px;background:linear-gradient(180deg,#a9c2d8,#c9b08a 50%,#7a6a4a)" role="img" aria-label="Woman holding wine in a hilltop vineyard"></div>
<div class="photo" style="left:615px;top:2998px;width:208px;height:173px;background:linear-gradient(135deg,#4a6a2a,#9aae5a 50%,#3a2a1a)" role="img" aria-label="Couple sharing wine among vines"></div>
<h3 class="post-title" style="left:335px;top:2785px">Vinoro Bistro italian restaurant</h3>
<p class="post-date" style="left:335px;top:2862px">Posted On 24th 2017</p>
<h3 class="post-title" style="left:840px;top:2785px">Vinoro Bistro italian restaurant</h3>
<p class="post-date" style="left:840px;top:2862px">Posted On 24th 2017</p>
<h3 class="post-title" style="left:335px;top:3023px">Vinoro Bistro italian restaurant</h3>
<p class="post-date" style="left:335px;top:3100px">Posted On 24th 2017</p>
<h3 class="post-title" style="left:840px;top:3023px">Vinoro Bistro italian restaurant</h3>
<p class="post-date" style="left:840px;top:3100px">Posted On 24th 2017</p>

<!-- Reservations -->
<section class="band soft" style="top:3313px;height:1009px"></section>
<h2 class="section-title" style="top:3400px">Reservations</h2>
<div class="rule" style="top:3465px"></div>
<form>
  <div class="field" style="left:190px;top:3520px;width:398px">Date</div>
  <div class="field" style="left:612px;top:3520px;width:398px">Phone Number (Optional)</div>
  <div class="field" style="left:190px;top:3617px;width:398px">Time</div>
  <div class="field" style="left:612px;top:3617px;width:398px">Hotel Name</div>
  <div class="field" style="left:190px;top:3710px;width:398px">Party Size
    <svg width="12" height="8" viewBox="0 0 12 8"><path d="M1 1l5 5 5-5" fill="none" stroke="#333" stroke-width="1.8"/></svg>
  </div>
  <div class="field" style="left:612px;top:3710px;width:398px">Room Number</div>
  <div class="field" style="left:190px;top:3804px;width:398px">Name</div>
  <div class="field" style="left:612px;top:3804px;width:398px">Guest Email</div>
  <div class="field" style="left:190px;top:3897px;width:820px">E-mail</div>
  <div class="field" style="left:190px;top:3977px;width:820px;height:162px">Comments (Optional)</div>
  <a class="btn" style="left:481px;top:4184px;width:238px;height:59px;font-size:17px">Submit</a>
</form>

<!-- Reviews -->
<svg class="abs" style="left:585px;top:4408px" width="30" height="30" viewBox="0 0 30 30"><circle cx="15" cy="15" r="13" fill="none" stroke="#222" stroke-width="3"/></svg>
<h2 class="section-title" style="top:4470px">Wandervane</h2>
<div class="rule" style="top:4530px"></div>

<svg class="abs" style="left:142px;top:4597px" width="20" height="20" viewBox="0 0 20 20"><path d="M10 1l2.6 6 6.4.5-4.9 4.2 1.5 6.3L10 14.6 4.4 18l1.5-6.3L1 7.5l6.4-.5z" fill="#222"/></svg>
<h3 class="rating-title" style="left:183px;top:4592px">Wandervane Traveler Rating</h3>
<p class="rating-sub" style="left:183px;top:4620px">Based on 1,096 traveler reviews</p>
<svg class="abs" style="left:142px;top:4680px" width="20" height="20" viewBox="0 0 20 20"><path d="M4 2h12v4a6 6 0 0 1-12 0zM10 12v4M6 18h8" fill="none" stroke="#222" stroke-width="2.4"/></svg>
<h3 class="rating-title" style="left:183px;top:4676px">Wandervane Ranking</h3>
<p class="rating-sub" style="left:183px;top:4704px">#8 of 571 places to eat in Cabo San Lucas</p>

<div class="reviews">
  <div class="reviews-head">Most Recent Traveler Reviews</div>
  <svg class="abs" style="left:573px;top:28px" width="40" height="14" viewBox="0 0 40 14"><path d="M7 1L1 7l6 6M33 1l6 6-6 6" fill="none" stroke="#222" stroke-width="2.2"/></svg>
  <span class="rev-date" style="left:30px">Jul 23, 2017</span>
  <span class="rev-quote" style="left:30px">"Delicious Italian!"</span>
  <span class="rev-date" style="left:255px">Jul 23, 2017</span>
  <span class="rev-quote" style="left:255px">"Our Landlord"</span>
  <span class="rev-date" style="left:456px">Jul 23, 2017</span>
  <span class="rev-quote" style="left:456px">"Best Italian in Cabo"</span>
</div>

<!-- Footer -->
<footer>
  <section class="band soft" style="top:4834px;height:266px"></section>
  <h4 class="foot-head" style="left:110px">Quick Links</h4>
  <ul class="foot-list" style="left:110px"><li>Home</li><li>Menu</li><li>Reservation</li></ul>
  <h4 class="foot-head" style="left:290px">Contact Us</h4>
  <ul class="foot-list" style="left:290px"><li>Tel: 555 0142</li><li>Calle Olivo 12, Centro</li><li>Cabo San Lucas, Mexico</li></ul>
  <h4 class="foot-head" style="left:512px">Locate Us</h4>
  <div class="photo" style="left:512px;top:4938px;width:294px;height:114px;background:linear-gradient(135deg,#e6e6e6,#cfd3d6)" role="img" aria-label="Street map of downtown Cabo San Lucas"></div>
  <div class="social-box">
    <span class="abs" style="left:16px;top:16px;width:36px;height:36px;background:var(--wine)"></span>
    <span class="abs" style="left:62px;top:16px;font-size:16px;color:var(--wine-text)">Vinoro Bistro</span>
    <span class="abs" style="left:62px;top:38px;font-family:Lato,Arial,sans-serif;font-size:11px;color:#777">Italian restaurant, Cabo</span>
    <div class="photo" style="left:16px;top:72px;width:50px;height:50px;background:#b79a84" role="img" aria-label="Follower photo"></div>
    <div class="photo" style="left:74px;top:72px;width:50px;height:50px;background:#8d7a6c" role="img" aria-label="Follower photo"></div>
    <div class="photo" style="left:132px;top:72px;width:50px;height:50px;background:#6f8aa4" role="img" aria-label="Follower photo"></div>
    <div class="photo" style="left:190px;top:72px;width:50px;height:50px;background:#a48e7a" role="img" aria-label="Follower photo"></div>
    <span class="abs" style="left:16px;top:138px;font-family:Lato,Arial,sans-serif;font-size:12px;color:#333">Like Us On Kindlepost</span>
  </div>

  <div class="brand" style="left:163px;top:5128px"><span class="brand-mark" style="width:10px;height:10px"></span><span class="brand-name" style="font-size:16px">Vinoro Bistro</span></div>
  <span class="legal" style="left:802px">Terms Of Conditions &nbsp;|&nbsp; Privacy Policy</span>
  <span class="legal" style="left:1134px">CS</span>
</footer>

</body>
</html>
```